Need A Standard Musical Download Website

We are looking for a talented designer to create a unique web design for our startup Music website called Vorde Sound.
The website should be responsive and filled with some creative stuffs along with bright colors.

Vorde sound is a website loaded with different types of music and capable of downloading the requested music by its users.
There will be categories of music which would be sorted by the genre. They include RnB, Hip-Hop, Afro pop, Pop, Dancehall and Reggae).

DESIGN STYLE/THEME

Creative, trendy, colorful, unique, and easy to use. You have freedom of selecting which ever color suits you. The design must be energetic and attractive.

NAVIGATION

HOME-MUSIC(RnB, Hip hop, Afro pop, POP, dancehall, Reggae)-ARTISTE-NEWS-LOGIN

PAGES REQUIRED
------------
1)Home Page
2)Music

FONTS
GOOGLE FONTS is strongly recommended.

Designers can get inspiration from https://tunabrook.example

Industry/Entity Type

Startup

```html
<!DOCTYPE html>
<html lang="en">
<head>
<meta charset="utf-8">
<title>Vorde Sound</title>
<link rel="stylesheet" href="https://fonts.googleapis.com/css2?family=Mukta:wght@700&family=Nunito+Sans:wght@400;600&family=Ubuntu:wght@500&display=swap">
<style>
:root{
  --red:#d10a0a;
  --ink:#111111;
  --nav:#8a8a8a;
  --dark-btn:#262626;
  --menu:#4e4e4e;
  --menu-line:#646464;
  --card-border:#cfcfcf;
  --muted:#8c8c8c;
  --footer:#efefef;
  --footer-ink:#444444;
}
*{margin:0;padding:0;box-sizing:border-box}
html,body{width:1200px;height:1086px;overflow:hidden;background:#fff}
body{position:relative;font-family:"Nunito Sans",sans-serif;color:var(--ink)}

.site-header{position:absolute;top:0;left:0;width:1200px;height:90px;background:#fff;border-bottom:1px solid #ddd;z-index:3}
.brand{position:absolute;left:115px;top:24px;font-size:36px;font-weight:400;color:var(--ink);letter-spacing:.3px}
.main-nav a{position:absolute;top:37px;font-size:16.5px;color:var(--nav);text-decoration:none;letter-spacing:.5px}
.main-nav a.active{color:var(--ink)}
.login-btn{position:absolute;left:971px;top:28px;width:106px;height:38px;background:var(--red);color:#fff;font-size:17px;display:flex;align-items:center;justify-content:center;letter-spacing:.5px}

.genre-menu{position:absolute;left:654px;top:77px;width:170px;height:200px;background:var(--menu);z-index:4;padding:15px 12px 0 12px}
.genre-menu::before{content:"";position:absolute;left:30px;top:-10px;border:12px solid transparent;border-top:0;border-bottom:10px solid var(--menu)}
.genre-menu li{list-style:none;height:29px;line-height:28px;padding-left:18px;color:#f2f2f2;font-size:14px;border-bottom:1px solid var(--menu-line)}
.genre-menu li:last-child{border-bottom:0}

.hero{position:absolute;left:0;top:90px;width:1200px;height:582px;background:linear-gradient(90deg,#4a1f1c 0%,#6a3530 22%,#5b4642 45%,#6d6460 62%,#8c8a74 82%,#5c5a4a 100%)}
.hero-title{position:absolute;left:128px;top:218px;font-family:"Mukta",sans-serif;font-weight:700;font-size:50px;line-height:51px;color:#fff}
.hero-btn{position:absolute;top:344px;height:46px;display:flex;align-items:center;justify-content:center;color:#fff;font-family:"Ubuntu",sans-serif;font-weight:500;font-size:19px}
.hero-btn.download{left:128px;width:174px;background:var(--red)}
.hero-btn.listen{left:311px;width:176px;background:linear-gradient(#3a3a3a,#151515)}
.slider-dots{position:absolute;left:556px;top:536px}

.features{position:absolute;left:117px;top:697px;width:966px;height:205px;border:1px solid var(--card-border);display:flex}
.feature{position:relative;flex:1;overflow:hidden;border-right:1px solid var(--card-border)}
.feature:last-child{border-right:0}
.feature.highlight{background:#f0f0f0}
.feature-art{position:absolute;right:0;top:0;height:100%}
.feature h2{position:absolute;left:32px;top:36px;font-weight:400;font-size:22px;line-height:26px;color:#222;z-index:1;white-space:nowrap}
.feature.highlight h2{color:var(--red)}
.feature p{position:absolute;left:32px;top:101px;width:170px;font-size:11px;line-height:16.5px;color:var(--muted);z-index:1}
.feature .btn{position:absolute;left:31px;top:141px;width:103px;height:31px;border:1px solid #c8c8c8;background:linear-gradient(#fff,#ececec);font-size:13.5px;color:#444;display:flex;align-items:center;justify-content:center;z-index:1}
.feature.highlight .btn{background:var(--red);border-color:var(--red);color:#fff}

.site-footer{position:absolute;left:0;top:956px;width:1200px;height:130px;background:var(--footer)}
.footer-nav a{position:absolute;top:39px;font-size:15px;color:var(--footer-ink);text-decoration:none}
.copyright{position:absolute;left:127px;top:67px;font-size:14px;color:#7a7a7a;word-spacing:1px}
.social{position:absolute;left:940px;top:35px}
</style>
</head>
<body>

<header class="site-header">
  <div class="brand">Vorde Sound</div>
  <nav class="main-nav">
    <a style="left:561px">HOME</a>
    <a class="active" style="left:661px">MUSIC</a>
    <a style="left:763px">ARTISTE</a>
    <a style="left:877px">NEWS</a>
  </nav>
  <div class="login-btn">LOGIN</div>
</header>

<ul class="genre-menu">
  <li>RnB</li><li>Hip hop</li><li>Afro pop</li><li>POP</li><li>Dancehall</li><li>Reggae</li>
</ul>

<section class="hero" role="img" aria-label="Photo of a bearded man in a plaid shirt listening to music on headphones">
  <h1 class="hero-title">Listen Different type of<br>Music and Download</h1>
  <div class="hero-btn download">Download</div>
  <div class="hero-btn listen">Listen Song</div>
  <svg class="slider-dots" width="90" height="16" viewBox="0 0 90 16">
    <circle cx="8" cy="8" r="6" fill="none" stroke="#fff" stroke-width="2"/>
    <circle cx="31" cy="8" r="7" fill="#fff"/>
    <circle cx="54" cy="8" r="7" fill="#fff"/>
    <circle cx="78" cy="8" r="7" fill="#fff"/>
  </svg>
</section>

<section class="features">
  <article class="feature">
    <div class="feature-art" role="img" aria-label="Colourful illustration of flying music notes" style="left:225px;background:radial-gradient(ellipse at 55% 50%,#f6c1b5 0%,#f7e3d8 45%,#fff 75%)"></div>
    <h2>Discover Your<br>Songs Collection</h2>
    <p>Class aptent taciti sociosqu ad litora torquent per con</p>
    <div class="btn">Read More</div>
  </article>
  <article class="feature highlight">
    <div class="feature-art" role="img" aria-label="Smartphone with earphones showing a music app" style="left:215px;background:radial-gradient(ellipse at 55% 45%,#3a3a3a 0%,#8c8c8c 30%,#f0f0f0 60%)"></div>
    <h2>Unlimited Songs<br>Download</h2>
    <p>Class aptent taciti sociosqu ad litora torquent per co</p>
    <div class="btn">Click here</div>
  </article>
  <article class="feature">
    <div class="feature-art" role="img" aria-label="Happy woman in a green top wearing headphones" style="left:215px;background:linear-gradient(90deg,#fff 0%,rgba(255,255,255,0) 40%),linear-gradient(180deg,#f4f4f4 0%,#d9c3b0 35%,#7aa4a8 65%,#1f9a3c 100%)"></div>
    <h2>Music by<br>Different Genre</h2>
    <p>Class aptent taciti sociosqu ad litora torquent per</p>
    <div class="btn">Read More</div>
  </article>
</section>

<footer class="site-footer">
  <nav class="footer-nav">
    <a style="left:127px">HOME</a>
    <a style="left:214px">MUSIC</a>
    <a style="left:302px">ARTISTE</a>
    <a style="left:400px">NEWS</a>
    <a style="left:484px">LOGIN</a>
    <a style="left:573px">CONTACT</a>
  </nav>
  <div class="copyright">© 2017 Company Name &nbsp;All right reserved &nbsp;Term of Use</div>
  <svg class="social" width="140" height="36" viewBox="0 0 140 36" aria-label="Social links">
    <g fill="none" stroke="#555" stroke-width="1.5">
      <circle cx="17" cy="18" r="16"/>
      <circle cx="52" cy="18" r="16"/>
      <circle cx="87" cy="18" r="16"/>
      <circle cx="122" cy="18" r="16"/>
    </g>
  </svg>
</footer>

</body>
</html>
```